e-commerce store for sport clothing online store "baseball merchandise "web application...

I want to design a UX/UI for my web application website for the online store I will provide you with the following:
1. screen shots of the initial design for the pages>
2. the logo files.
3. The brand guideline file.

the provided files (screen shots) is guideline I want to see CREATIVITY with the UX/UI DESIGN.
PS. PLEASE FOLLOW THE BRANDGUIDE LINE CAREFULLY SPECIALLY THE TYPOGRAPHY & THE COLOR CODES.

PLEASE VISIT THIS WEBSITE brightlane.varomi-qz.com to see more for the screens.

```html
<!DOCTYPE html>
<html lang="en">
<head>
<meta charset="UTF-8">
<title>Shopping Cart</title>
<link href="https://fonts.googleapis.com/css2?family=Lato:wght@400;700;900&display=swap" rel="stylesheet">
<style>
  :root {
    --navy: #0d2146;
    --ink: #111111;
    --muted: #555555;
    --selected-bg: #b8b8b8;
    --card-border: #c9c9c9;
    --white: #ffffff;
    --danger: #b3133b;
    --page: #ffffff;
  }
  * { box-sizing: border-box; margin: 0; padding: 0; }
  html, body {
    width: 1200px; height: 2667px; overflow: hidden;
    background: var(--page);
    font-family: 'Lato', sans-serif;
    color: var(--ink);
  }
  .screen {
    position: absolute; left: 0; top: 0;
    width: 360px; height: 800px;
    transform: scale(3.33334); transform-origin: 0 0;
    background: var(--page);
  }
  .app-header {
    position: absolute; left: 0; top: 0; width: 360px; height: 80px;
    background: var(--navy);
  }
  .back-button { position: absolute; left: 22px; top: 31px; width: 20px; height: 20px; }
  .app-title {
    position: absolute; left: 0; right: 0; top: 30px; text-align: center;
    color: var(--white); font-weight: 700; font-size: 16px; letter-spacing: 0.2px;
  }
  .select-all { position: absolute; left: 13px; top: 91px; display: flex; align-items: center; gap: 10px; font-size: 14px; }
  .radio { width: 19px; height: 19px; border: 1.5px solid #222; border-radius: 50%; }
  .selected-count { position: absolute; right: 8px; top: 93px; font-size: 13px; font-weight: 700; }

  .cart-item {
    position: absolute; left: 7px; width: 346px; height: 124px;
    border: 1px solid var(--card-border); border-radius: 6px; background: var(--white);
  }
  .cart-item.is-selected { background: var(--selected-bg); border-color: #9a9a9a; }
  .item-check { position: absolute; left: 5px; top: 5px; width: 21px; height: 21px; z-index: 2; }
  .item-photo { position: absolute; border-radius: 3px; z-index: 1; }
  .item-name { position: absolute; left: 126px; font-size: 14px; font-weight: 900; line-height: 18px; width: 150px; }
  .qty { position: absolute; left: 127px; display: flex; align-items: center; gap: 5px; }
  .qty-btn { width: 15px; height: 15px; }
  .qty-value {
    width: 20px; height: 17px; border: 1px solid #777; font-size: 12px;
    display: flex; align-items: center; justify-content: center; background: #f3f3f3;
  }
  .item-price { position: absolute; right: 12px; font-size: 15px; font-weight: 900; color: var(--navy); }

  .voucher-input {
    position: absolute; left: 12px; top: 413px; width: 248px; height: 35px;
    border: 1px solid #777; border-radius: 4px; padding-left: 11px;
    display: flex; align-items: center; font-size: 12px; color: var(--ink);
  }
  .apply-button {
    position: absolute; left: 274px; top: 413px; width: 79px; height: 35px;
    background: var(--navy); border-radius: 4px; color: var(--white);
    font-weight: 700; font-size: 14px; display: flex; align-items: center; justify-content: center;
  }
  .summary { position: absolute; left: 11px; top: 476px; width: 320px; }
  .summary-row { display: flex; justify-content: space-between; font-size: 13px; height: 27px; }
  .summary-row .amount { color: var(--navy); font-weight: 700; }

  .action-bar {
    position: absolute; left: 0; top: 735px; width: 360px; height: 65px; background: var(--white);
    box-shadow: 0 -14px 16px rgba(0,0,0,0.06);
  }
  .remove-action { position: absolute; left: 26px; top: 21px; display: flex; align-items: center; gap: 9px; color: var(--danger); font-weight: 700; font-size: 16px; }
  .checkout-button {
    position: absolute; left: 177px; top: 11px; width: 172px; height: 44px;
    background: #000; border-radius: 4px; color: var(--white); font-weight: 700; font-size: 14px;
    display: flex; align-items: center; justify-content: center;
  }
</style>
</head>
<body>
<div class="screen">
  <header class="app-header">
    <svg class="back-button" viewBox="0 0 20 20"><path d="M17 10H4M9 4l-6 6 6 6" fill="none" stroke="#fff" stroke-width="2" stroke-linecap="round" stroke-linejoin="round"/></svg>
    <h1 class="app-title">Shopping Cart</h1>
  </header>

  <div class="select-all"><span class="radio"></span><span>All</span></div>
  <div class="selected-count">1 Selected</div>

  <article class="cart-item is-selected" style="top:120px;">
    <div class="item-photo" role="img" aria-label="Green kids swim trunks product photo" style="left:20px;top:5px;width:93px;height:97px;background:linear-gradient(135deg,#6fae93,#4d8f74 60%,#9a8a7a);"></div>
    <svg class="item-check" viewBox="0 0 21 21"><circle cx="10.5" cy="10.5" r="10" fill="#111"/><path d="M6 10.8l3 3 6-6.3" fill="none" stroke="#fff" stroke-width="2" stroke-linecap="round" stroke-linejoin="round"/></svg>
    <h2 class="item-name" style="top:22px;">Splashby Kids Swim Trunks</h2>
    <div class="qty" style="top:76px;">
      <svg class="qty-btn" viewBox="0 0 15 15"><circle cx="7.5" cy="7.5" r="6.7" fill="none" stroke="#111" stroke-width="1.3"/><path d="M4.5 7.5h6" stroke="#111" stroke-width="1.5"/></svg>
      <span class="qty-value">1</span>
      <svg class="qty-btn" viewBox="0 0 15 15"><circle cx="7.5" cy="7.5" r="7.5" fill="var(--navy)"/><path d="M4.3 7.5h6.4M7.5 4.3v6.4" stroke="#fff" stroke-width="1.5"/></svg>
    </div>
    <div class="item-price" style="top:97px;">23.000 KD</div>
  </article>

  <article class="cart-item" style="top:260px;">
    <div class="item-photo" role="img" aria-label="Grey and white trucker cap product photo" style="left:20px;top:7px;width:80px;height:96px;background:radial-gradient(circle at 50% 50%,#c5cdd6,#eef0f2 70%);box-shadow:0 1px 4px rgba(0,0,0,0.35);"></div>
    <svg class="item-check" viewBox="0 0 21 21"><circle cx="10" cy="10" r="9" fill="#9c9c9c" stroke="#777" stroke-width="1"/></svg>
    <h2 class="item-name" style="top:22px;">Bass Trucker Cap</h2>
    <div class="qty" style="top:77px;">
      <svg class="qty-btn" viewBox="0 0 15 15"><circle cx="7.5" cy="7.5" r="6.7" fill="none" stroke="#111" stroke-width="1.3"/><path d="M4.5 7.5h6" stroke="#111" stroke-width="1.5"/></svg>
      <span class="qty-value">2</span>
      <svg class="qty-btn" viewBox="0 0 15 15"><circle cx="7.5" cy="7.5" r="7.5" fill="var(--navy)"/><path d="M4.3 7.5h6.4M7.5 4.3v6.4" stroke="#fff" stroke-width="1.5"/></svg>
    </div>
    <div class="item-price" style="top:97px;">13.000 KD</div>
  </article>

  <div class="voucher-input">Enter Voucher Code</div>
  <div class="apply-button">Apply</div>

  <section class="summary">
    <div class="summary-row"><span>Subtotal</span><span class="amount">23.000 KD</span></div>
    <div class="summary-row"><span>Delivery Charge</span><span class="amount">1.000 KD</span></div>
    <div class="summary-row"><span>Total</span><span class="amount">24.000 KD</span></div>
  </section>

  <footer class="action-bar">
    <div class="remove-action">
      <svg width="24" height="25" viewBox="0 0 24 25"><path d="M3 5h18M9 5V2.5h6V5M5 5l1.2 18h11.6L19 5M10 9v10M14 9v10" fill="none" stroke="var(--danger)" stroke-width="1.8" stroke-linejoin="round"/></svg>
      <span>Remove</span>
    </div>
    <div class="checkout-button">Go to Checkout</div>
  </footer>
</div>
</body>
</html>
```